Drone service provider needs a brilliant web design

I need a responsive web design for a new drone service company. Pelham Drone Solutions provides turnkey solutions to capture, process, and deliver actionable aerial data to customers. The design should communicate a professional company that is safe, legal and insured. I included our logo design and business card designs for reference.
*content to be supplied after design selected

Target Market(s)

We serve telecommunications, construction, government, utility infrastructure, insurance and other industries.

Industry/Entity Type

Industrial

Number of Pages Required

5+ page

Colors

Designer to choose colors to be used in the design.

Requirements
Must have
• The design should highlight professional services to include Inspections, Mapping, Consulting and Training. The site should include aerial images and video to compliment the services offered. The landing page must include following sections in order: HOME, SERVICES, ABOUT, DEMO REEL, CLIENTS, CONTACT FORM, and social media buttons (Facebook, LinkedIn, Twitter, YouTube, Instagram). Contact: 615-382-9041 info@pelhamdronesolutions-example.com Smyrna, TN
• Sitemap:
• 6 pages: Home, Inspections, Mapping, Training, Consulting, About
• HOME (Landing Page)
• • Header with logo and tab links (Home, Services, About, Contact)
• • 'CAPTURE. PROCESS. DELIVER.' tagline and 'CONTACT US' button displayed within aerial image of drone over city or construction site
• • Services section with icons, text and read more link to page
• • About section with photo and text with three icons for SAFE. LEGAL. INSURED.
• • Demo reel
• • Clients logos shown scrolling horizontally
• • Contact form
• • Footer with logo, phone, email, social media buttons
• SERVICES (4 different pages)
• • Inspections
• • Mapping
• • Consulting
• • Training
• ABOUT page
• • Company
• • Partners
• • Certifications & Associations
• • Careers
• CONTACT linked to bottom of landing page
• Would you like to receive the newsletter? Yes or No Drop-down list
Nice to have
• Photos of KVR Marlin or Corvex inspecting infrastructure, buildings, construction sites, etc. A photo of one or two pilots in vest and helmet. Free stock photos preferred but would purchase the right photo that's more relevant.
• website references:
• https://www.quillrotor-example.com/
• https://www.brentfieldworks-example.com/services
• https://www.tomaro-example.com/
• http://gantrymetric-example.com/
• http://lumbrook-example.com/
• http://fennotics-example.com/
• https://www.grebe-example.io/
Should not have
• not an aerial photography or videography service business, no blog or newsletter

```html
<!DOCTYPE html>
<html lang="en">
<head>
<meta charset="utf-8">
<title>Training — Pelham Drone Solutions</title>
<link rel="stylesheet" href="https://fonts.googleapis.com/css2?family=Montserrat:wght@400;600;700;800&family=Open+Sans:wght@400;600&display=swap">
<style>
  :root {
    --brand-blue: #1b8dcf;
    --brand-blue-deep: #0f6fae;
    --ink: #2b2b2b;
    --body-ink: #3a3a3a;
    --white: #ffffff;
    --footer-bg: #252525;
    --footer-rule: #8a8a8a;
    --photo-grey: #6d7580;
  }
  * { box-sizing: border-box; margin: 0; padding: 0; }
  html, body { width: 1200px; height: 2853px; overflow: hidden; }
  body { position: relative; background: var(--white); font-family: "Open Sans", Arial, sans-serif; color: var(--body-ink); }

  /* Header */
  .site-header { position: absolute; left: 0; top: 0; width: 1200px; height: 118px; background: var(--brand-blue); z-index: 3; }
  .main-nav { position: absolute; left: 99px; top: 48px; display: flex; gap: 40px; }
  .main-nav a { color: var(--white); text-decoration: none; font: 600 15px "Montserrat", Arial, sans-serif; letter-spacing: .3px; }
  .logo-plate { position: absolute; left: 395px; top: 0; width: 410px; height: 164px; }
  .brand-name { position: absolute; left: 0; width: 1200px; text-align: center; font-family: "Montserrat", Arial, sans-serif; font-weight: 800; text-transform: uppercase; }
  .brand-name--header { top: 30px; font-size: 34px; line-height: 1; color: #222; letter-spacing: 1px; }
  .brand-name--header small, .brand-name--footer small { display: block; font-size: 13px; letter-spacing: 3px; margin-top: 4px; }
  .social { position: absolute; display: flex; gap: 12px; }
  .social--header { left: 877px; top: 42px; }
  .social span { width: 34px; height: 34px; border: 2px solid var(--white); border-radius: 50%; display: block; }

  /* Hero */
  .hero { position: absolute; left: 0; top: 118px; width: 1200px; height: 287px; }
  .hero-photo { position: absolute; inset: 0; background: linear-gradient(180deg, #9aa3ab 0%, #7d8a96 45%, #5f6b74 75%, #8b949b 100%); }
  .hero-band { position: absolute; left: 0; bottom: 0; width: 1200px; height: 287px; }
  .hero-title { position: absolute; left: 97px; top: 135px; color: var(--white); font: 800 58px "Montserrat", Arial, sans-serif; letter-spacing: 1px; }

  /* Intro */
  .intro { position: absolute; left: 0; top: 470px; width: 1200px; text-align: center; }
  .intro h2 { color: var(--brand-blue); font: 700 28px "Montserrat", Arial, sans-serif; }
  .intro .rule { width: 112px; height: 3px; background: var(--brand-blue); margin: 14px auto 0; }
  .intro p { width: 960px; margin: 34px auto 0; font-size: 13.5px; line-height: 22px; color: var(--body-ink); }

  /* Course rows */
  .course { position: absolute; left: 0; width: 1200px; }
  .course--blue { background: var(--brand-blue); color: var(--white); }
  .course-photo { position: absolute; }
  .course-copy { position: absolute; width: 623px; }
  .course-copy h3 { font: 700 27px "Montserrat", Arial, sans-serif; color: var(--brand-blue); }
  .course--blue .course-copy h3 { color: var(--white); }
  .course-copy h4 { font: 600 19px "Montserrat", Arial, sans-serif; color: var(--ink); margin-top: 8px; }
  .course--blue .course-copy h4 { color: var(--white); }
  .course-copy p { font-size: 13.5px; line-height: 22.5px; text-align: justify; margin-top: 22px; }
  .course-copy h4 + p { margin-top: 24px; }

  /* Footer */
  .site-footer { position: absolute; left: 0; top: 2442px; width: 1200px; height: 411px; background: var(--footer-bg); color: var(--white); border-top: 3px solid var(--white); }
  .brand-name--footer { top: 82px; font-size: 40px; line-height: 1; color: var(--white); letter-spacing: 1px; }
  .contact-row { position: absolute; top: 195px; left: 0; width: 1200px; display: flex; justify-content: center; gap: 30px; font-size: 20px; }
  .contact-row .item { display: flex; align-items: center; gap: 12px; }
  .contact-row svg { width: 34px; height: 34px; }
  .footer-nav { position: absolute; top: 277px; left: 0; width: 1200px; display: flex; justify-content: center; font: 600 15px "Montserrat", Arial, sans-serif; }
  .footer-nav a { color: var(--white); text-decoration: none; }
  .footer-nav .sep { margin: 0 80px; }
  .footer-rule { position: absolute; left: 97px; top: 334px; width: 1003px; height: 1px; background: var(--footer-rule); }
  .copyright { position: absolute; left: 97px; top: 360px; font-size: 14px; font-weight: 600; }
  .social--footer { left: 915px; top: 351px; gap: 10px; }
  .social--footer span { width: 30px; height: 30px; }
</style>
</head>
<body>

<header class="site-header">
  <nav class="main-nav">
    <a href="#">HOME</a><a href="#">SERVICES</a><a href="#">ABOUT</a>
  </nav>
  <svg class="logo-plate" viewBox="0 0 410 164" aria-hidden="true">
    <path d="M0 0 H410 L380 118 C355 150 300 164 205 164 C110 164 55 150 30 118 Z" fill="#ffffff"/>
  </svg>
  <div class="brand-name brand-name--header">Pelham<small>Drone Solutions</small></div>
  <div class="social social--header" aria-label="Social media links">
    <span></span><span></span><span></span><span></span><span></span>
  </div>
</header>

<section class="hero">
  <div class="hero-photo" role="img" aria-label="Aerial city harbour skyline with a drone flying over a construction site"></div>
  <svg class="hero-band" viewBox="0 0 1200 287" preserveAspectRatio="none" aria-hidden="true">
    <path d="M0 190 L420 250 L420 287 L0 287 Z" fill="#1b8dcf" opacity=".55"/>
    <path d="M0 278 C300 272 700 268 1200 262" stroke="#1b8dcf" stroke-width="3" fill="none"/>
  </svg>
  <h1 class="hero-title">TRAINING</h1>
</section>

<section class="intro">
  <h2>TRAINING</h2>
  <div class="rule"></div>
  <p>Nam libero tempore, cum soluta nobis est eligendi optio cumque nihil impedit quo minus id quod maxime placeat facere possimus, omnis voluptas assumenda est, omnis dolor repellendus.</p>
</section>

<section class="course" style="top:608px;height:452px;">
  <div class="course-photo" role="img" aria-label="Student writing notes while studying for the exam"
       style="left:757px;top:0;width:443px;height:452px;background:linear-gradient(135deg,#7f8a6a 0%,#c9b49a 45%,#e9e4de 100%);clip-path:polygon(0 8%,100% 0,100% 100%,0 92%);"></div>
  <div class="course-copy" style="left:97px;top:76px;">
    <h3>FAA Part 107 Exam preparation</h3>
    <h4>Nemo enim ipsam voluptatem quia voluptas aspernatur</h4>
    <p>Nemo enim ipsam voluptatem quia voluptas sit aspernatur aut odit aut fugit, sed quia consequuntur magni dolores eos qui ratione voluptatem sequi nesciunt. Neque porro quisquam est, qui dolorem ipsum quia dolor sit amet, consectetur, adipisci velit, sed quia non numquam eius modi tempora incidunt ut labore et dolore magnam aliquam quaerat voluptatem.</p>
    <p>Ipsam voluptatem quia voluptas sit aspernatur aut odit aut fugit, sed quia consequuntur magni dolores eos qui ratione voluptatem sequi nesciunt. Neque porro quisquam est, qui dolorem ipsum quia dolor sit amet, consectetur, adipisci velit, sed quia non numquam eius modi tempora incidunt ut labore et dolore magnam aliquam quaerat voluptatem.</p>
  </div>
</section>

<section class="course course--blue" style="top:1065px;height:456px;">
  <div class="course-photo" role="img" aria-label="Pilot reviewing a checklist in front of a cockpit instrument panel"
       style="left:0;top:0;width:447px;height:456px;background:linear-gradient(120deg,#e8eaec 0%,#4a4f58 40%,#1e2126 100%);clip-path:polygon(0 0,100% 8%,100% 92%,0 100%);"></div>
  <div class="course-copy" style="left:477px;top:80px;">
    <h3>Flight Operations</h3>
    <h4>Nemo enim ipsam voluptatem quia voluptas</h4>
    <p>Nemo enim ipsam voluptatem quia voluptas sit aspernatur aut odit aut fugit, sed quia consequuntur magni dolores eos qui ratione voluptatem sequi nesciunt. Neque porro quisquam est, qui dolorem ipsum quia dolor sit amet, consectetur, adipisci velit, sed quia non numquam eius modi tempora incidunt ut labore et dolore magnam aliquam quaerat voluptatem.</p>
    <p>Ipsam voluptatem quia voluptas sit aspernatur aut odit aut fugit, sed quia consequuntur magni dolores eos qui ratione voluptatem sequi nesciunt. Neque porro quisquam est, qui dolorem ipsum quia dolor sit amet, consectetur, adipisci velit, sed quia non numquam eius modi tempora incidunt ut labore et dolore magnam aliquam quaerat voluptatem.</p>
  </div>
</section>

<section class="course" style="top:1521px;height:457px;">
  <div class="course-photo" role="img" aria-label="Hand touching a risk concept interface with business icons"
       style="left:757px;top:30px;width:443px;height:400px;background:linear-gradient(135deg,#3b4048 0%,#7c838d 50%,#c9ced4 100%);clip-path:polygon(0 8%,100% 0,100% 100%,0 92%);"></div>
  <div class="course-copy" style="left:97px;top:84px;">
    <h3>Risk Management</h3>
    <h4>Nemo enim ipsam voluptatem quia voluptas</h4>
    <p>Nemo enim ipsam voluptatem quia voluptas sit aspernatur aut odit aut fugit, sed quia consequuntur magni dolores eos qui ratione voluptatem sequi nesciunt. Neque porro quisquam est, qui dolorem ipsum quia dolor sit amet, consectetur, adipisci velit, sed quia non numquam eius modi tempora incidunt ut labore et dolore magnam aliquam quaerat voluptatem.</p>
    <p>Ipsam voluptatem quia voluptas sit aspernatur aut odit aut fugit, sed quia consequuntur magni dolores eos qui ratione voluptatem sequi nesciunt. Neque porro quisquam est, qui dolorem ipsum quia dolor sit amet, consectetur, adipisci velit, sed quia non numquam eius modi tempora incidunt ut labore et dolore magnam aliquam quaerat voluptatem.</p>
  </div>
</section>

<section class="course course--blue" style="top:1978px;height:460px;">
  <div class="course-photo" role="img" aria-label="Colleagues reviewing fleet data together on a tablet"
       style="left:0;top:0;width:447px;height:460px;background:linear-gradient(120deg,#4b3a2e 0%,#b59a82 45%,#d8d6d2 100%);clip-path:polygon(0 0,100% 8%,100% 92%,0 100%);"></div>
  <div class="course-copy" style="left:477px;top:88px;">
    <h3>Fleet Management</h3>
    <h4>Nemo enim ipsam voluptatem quia voluptas</h4>
    <p>Nemo enim ipsam voluptatem quia voluptas sit aspernatur aut odit aut fugit, sed quia consequuntur magni dolores eos qui ratione voluptatem sequi nesciunt. Neque porro quisquam est, qui dolorem ipsum quia dolor sit amet, consectetur, adipisci velit, sed quia non numquam eius modi tempora incidunt ut labore et dolore magnam aliquam quaerat voluptatem.</p>
    <p>Ipsam voluptatem quia voluptas sit aspernatur aut odit aut fugit, sed quia consequuntur magni dolores eos qui ratione voluptatem sequi nesciunt. Neque porro quisquam est, qui dolorem ipsum quia dolor sit amet, consectetur, adipisci velit, sed quia non numquam eius modi tempora incidunt ut labore et dolore magnam aliquam quaerat voluptatem.</p>
  </div>
</section>

<footer class="site-footer">
  <div class="brand-name brand-name--footer">Pelham<small>Drone Solutions</small></div>
  <div class="contact-row">
    <div class="item">
      <svg viewBox="0 0 34 34" aria-hidden="true"><circle cx="17" cy="17" r="15.5" fill="none" stroke="#fff" stroke-width="2"/><rect x="9" y="11.5" width="16" height="11" rx="1.5" fill="none" stroke="#fff" stroke-width="1.8"/><path d="M9.5 12.5 L17 18 L24.5 12.5" fill="none" stroke="#fff" stroke-width="1.8"/></svg>
      <span>info@pelhamdronesolutions-example.com</span>
    </div>
    <div class="item">
      <svg viewBox="0 0 34 34" aria-hidden="true"><circle cx="17" cy="17" r="15.5" fill="none" stroke="#fff" stroke-width="2"/><path d="M12.5 9.5 L15 9.5 L16.3 13 L14.6 14.4 C15.5 16.5 17.5 18.5 19.6 19.4 L21 17.7 L24.5 19 L24.5 21.5 C24.5 23 23 24.3 21.5 24 C15.5 23 11 18.5 10 12.5 C9.8 11 11 9.5 12.5 9.5 Z" fill="none" stroke="#fff" stroke-width="1.7" stroke-linejoin="round"/></svg>
      <span>615-382-9041</span>
    </div>
  </div>
  <nav class="footer-nav">
    <a href="#">HOME</a><span class="sep">|</span><a href="#">SERVICES</a><span class="sep">|</span><a href="#">ABOUT</a><span class="sep">|</span><a href="#">CONTACT US</a>
  </nav>
  <div class="footer-rule"></div>
  <p class="copyright">Copyright © 2018 Pelham Drone Solutions. All Right Reserved</p>
  <div class="social social--footer" aria-label="Social media links">
    <span></span><span></span><span></span><span></span><span></span>
  </div>
</footer>

</body>
</html>
```